SkyvornQ Business Cards and Stationary Design

Need a design for our business cards and stationary. I want to carry on the theme of the logo. I want the business cards to have a design on the back. I would like the business cards and the stationary to carry the same theme, design scheme, and branding

Target Market(s)

Airlines and Maintenance Facilities

Industry/Entity Type

Aviation

Contact Information for Business Card

Name
Position Title
Address: 4827 Trellis Hollow Road, Brenwick Falls, Tallmere, 34951
Office Number
Mobile Number
Email
Website

Font styles to use
Serif
Sans Serif

Colors

Designer to choose colors to be used in the design.

```html
<!DOCTYPE html>
<html lang="en">
<head>
<meta charset="utf-8">
<title>SkyvornQ Business Card</title>
<link rel="stylesheet" href="https://fonts.googleapis.com/css2?family=Open+Sans:wght@400;700&display=swap">
<style>
  :root {
    --backdrop: #e6e3e0;
    --card: #ffffff;
    --navy: #0d2d6b;
    --sky: #1f7fcf;
    --ink: #4a4f57;
    --edge: rgba(0,0,0,0.12);
  }
  * { margin: 0; padding: 0; box-sizing: border-box; }
  html, body {
    width: 1200px; height: 997px; overflow: hidden;
    background: var(--backdrop);
    font-family: "Open Sans", Arial, sans-serif;
  }
  .canvas { position: relative; width: 1200px; height: 997px; }
  .card {
    position: absolute;
    width: 540px; height: 309px;
    background: var(--card);
    box-shadow: 0 10px 24px var(--edge);
    overflow: hidden;
  }
  .card--contact { left: 50px; top: 190px; }
  .card--brand { left: 610px; top: 500px; }

  .name-band {
    position: absolute; left: 0; right: 0; top: 64px; height: 36px;
    background: var(--navy);
    display: flex; align-items: center; padding-left: 40px; gap: 12px;
    color: #fff;
  }
  .name-band .person { font-weight: 700; font-size: 18px; letter-spacing: 0.3px; }
  .name-band .role { font-size: 13px; }
  .band-mark {
    position: absolute; right: 34px; top: 58px;
    width: 48px; height: 48px; border-radius: 50%;
    background: var(--card); border: 5px solid var(--sky);
  }

  .contact-list {
    position: absolute; left: 40px; top: 168px;
    list-style: none; font-size: 13.5px; color: var(--ink); line-height: 19px;
  }
  .contact-list li { display: flex; align-items: center; gap: 8px; }
  .contact-list svg { width: 11px; height: 11px; fill: var(--navy); flex: none; }
  .address {
    position: absolute; left: 59px; top: 256px;
    font-size: 13.5px; color: var(--ink);
  }

  .brand-lockup {
    position: absolute; inset: 0;
    display: flex; flex-direction: column; align-items: center; justify-content: center; gap: 16px;
  }
  .brand-dot {
    width: 74px; height: 74px; border-radius: 50%;
    border: 7px solid var(--sky);
  }
  .brand-name {
    font-weight: 700; font-size: 40px; letter-spacing: 6px; color: var(--navy);
  }
</style>
</head>
<body>
<main class="canvas">
  <section class="card card--contact" aria-label="Business card, contact side">
    <div class="name-band">
      <span class="person">MARLOW TESSEN</span>
      <span class="role">President</span>
    </div>
    <div class="band-mark" aria-hidden="true"></div>
    <ul class="contact-list">
      <li><svg viewBox="0 0 12 12"><path d="M2 1h3l1 3-2 1a7 7 0 0 0 3 3l1-2 3 1v3c-6 0-9-3-9-9z"/></svg>001 555 0187</li>
      <li><svg viewBox="0 0 12 12"><path d="M3 0h6a1 1 0 0 1 1 1v10a1 1 0 0 1-1 1H3a1 1 0 0 1-1-1V1a1 1 0 0 1 1-1zm0 2v7h6V2z"/></svg>001 555 0187</li>
      <li><svg viewBox="0 0 12 12"><path d="M0 2h12v8H0zm1 1 5 4 5-4z"/></svg>info@skyvornq.com</li>
      <li><svg viewBox="0 0 12 12"><circle cx="6" cy="6" r="5.5"/></svg>www.skyvornq.com</li>
    </ul>
    <p class="address">4827 Trellis Hollow Road, Brenwick Falls, Tallmere, 34951</p>
  </section>

  <section class="card card--brand" aria-label="Business card, brand side">
    <div class="brand-lockup">
      <div class="brand-dot" aria-hidden="true"></div>
      <div class="brand-name">SKYVORNQ</div>
    </div>
  </section>
</main>
</body>
</html>
```